One business card required with 2 company logos and 2 people's details

One business card required.
No preference on design - One side could show the 2 different business logos for the companies we own. The reverse could have the details shown below.
Another option could be one business one side and one business on the reverse. Happy to receive designs.

Dora Pellham
07700 913 286
Rowena Tindall
07700 958 137

website: quietmeadowbloom.co.uk
email: info@quietmeadowbloom.co.uk

website: brightharbourevents.co.uk
email: info:brightharbourevents.co.uk

May be nice to have icons instead of the words email/website?

I have included different versions of the logos to help with your design.

Contact Information for Business Card

see project overview

Requirements
Must have
• both company logos, both contact names and contact details

```html
<!DOCTYPE html>
<html lang="en">
<head>
<meta charset="utf-8">
<title>Business Card – Bright Harbour Events &amp; Quiet Meadow Bloom</title>
<link rel="stylesheet" href="https://fonts.googleapis.com/css2?family=Poppins:wght@400;600;700&display=swap">
<style>
  :root {
    --bg: #666666;
    --card: #ffffff;
    --card-edge: #1a4fd0;
    --name-blue: #1a8ae6;
    --ink: #1d1d1f;
    --muted: #444444;
    --icon-teal: #1fb6d6;
    --brand-blue: #1846d8;
    --brand-navy: #1b1a3d;
    --feather-a: #e6f6fb;
    --feather-b: #d9def7;
    --feather-c: #e8dcf5;
  }
  * { box-sizing: border-box; margin: 0; padding: 0; }
  html, body { width: 1200px; height: 800px; overflow: hidden; }
  body {
    background: var(--bg);
    font-family: "Poppins", sans-serif;
    position: relative;
  }
  .card {
    position: absolute;
    left: 290px;
    width: 620px;
    height: 354px;
    background: var(--card);
    border-radius: 22px;
    border-bottom: 3px solid var(--card-edge);
    box-shadow: 0 10px 24px rgba(0,0,0,0.35);
    overflow: hidden;
  }
  .card--contacts { top: 30px; }
  .card--brands { top: 414px; }

  /* Contacts side */
  .feather-art {
    position: absolute;
    left: 150px;
    bottom: -30px;
    width: 380px;
    height: 170px;
    border-radius: 50% 50% 40% 60% / 70% 60% 40% 30%;
    background: linear-gradient(100deg, var(--feather-a), var(--feather-b) 55%, var(--feather-c));
    transform: rotate(-18deg);
    opacity: 0.85;
  }
  .people {
    position: absolute;
    left: 40px;
    bottom: 46px;
  }
  .person + .person { margin-top: 12px; }
  .person__name {
    color: var(--name-blue);
    font-weight: 700;
    font-size: 27px;
    line-height: 1.1;
  }
  .person__phone {
    display: flex;
    align-items: center;
    gap: 8px;
    color: var(--ink);
    font-weight: 600;
    font-size: 19px;
    line-height: 1.3;
  }
  .person__phone svg { width: 14px; height: 14px; fill: var(--name-blue); }

  .links {
    position: absolute;
    right: 36px;
    top: 118px;
    list-style: none;
    text-align: right;
  }
  .links li {
    display: flex;
    justify-content: flex-end;
    align-items: center;
    gap: 8px;
    color: var(--muted);
    font-size: 15.5px;
    line-height: 1.55;
  }
  .links svg { width: 15px; height: 15px; flex: none; }

  /* Brands side */
  .brands {
    position: absolute;
    inset: 0;
    display: flex;
    align-items: center;
    justify-content: center;
  }
  .brand {
    width: 270px;
    text-align: center;
    font-weight: 600;
    font-size: 30px;
    line-height: 1.15;
  }
  .brand--events { color: var(--brand-blue); }
  .brand--bloom { color: var(--brand-navy); }
  .brands__divider {
    width: 1px;
    height: 150px;
    background: var(--brand-blue);
    margin: 0 16px;
  }
</style>
</head>
<body>

<section class="card card--contacts" aria-label="Contact side">
  <div class="feather-art" role="img" aria-label="Soft pastel feather illustration"></div>

  <div class="people">
    <div class="person">
      <p class="person__name">Rowena Tindall</p>
      <p class="person__phone">
        <svg viewBox="0 0 24 24" aria-hidden="true"><path d="M6.6 10.8a15 15 0 0 0 6.6 6.6l2.2-2.2a1 1 0 0 1 1-.25 11.4 11.4 0 0 0 3.6.57 1 1 0 0 1 1 1V20a1 1 0 0 1-1 1A17 17 0 0 1 3 4a1 1 0 0 1 1-1h3.5a1 1 0 0 1 1 1c0 1.25.2 2.45.57 3.57a1 1 0 0 1-.25 1z"/></svg>
        07700 958 137
      </p>
    </div>
    <div class="person">
      <p class="person__name">Dora Pellham</p>
      <p class="person__phone">
        <svg viewBox="0 0 24 24" aria-hidden="true"><path d="M6.6 10.8a15 15 0 0 0 6.6 6.6l2.2-2.2a1 1 0 0 1 1-.25 11.4 11.4 0 0 0 3.6.57 1 1 0 0 1 1 1V20a1 1 0 0 1-1 1A17 17 0 0 1 3 4a1 1 0 0 1 1-1h3.5a1 1 0 0 1 1 1c0 1.25.2 2.45.57 3.57a1 1 0 0 1-.25 1z"/></svg>
        07700 913 286
      </p>
    </div>
  </div>

  <ul class="links">
    <li>info@quietmeadowbloom.co.uk
      <svg viewBox="0 0 16 16" aria-hidden="true"><rect x="1" y="3" width="14" height="10" rx="1.5" fill="var(--icon-teal)"/><path d="M1.5 4l6.5 5 6.5-5" stroke="#fff" stroke-width="1.3" fill="none"/></svg>
    </li>
    <li>quietmeadowbloom.co.uk
      <svg viewBox="0 0 16 16" aria-hidden="true"><circle cx="8" cy="8" r="7" fill="var(--icon-teal)"/><path d="M1 8h14M8 1c-3 3.5-3 10.5 0 14M8 1c3 3.5 3 10.5 0 14" stroke="#fff" stroke-width="1" fill="none"/></svg>
    </li>
    <li>info:brightharbourevents.co.uk
      <svg viewBox="0 0 16 16" aria-hidden="true"><rect x="1" y="3" width="14" height="10" rx="1.5" fill="var(--icon-teal)"/><path d="M1.5 4l6.5 5 6.5-5" stroke="#fff" stroke-width="1.3" fill="none"/></svg>
    </li>
    <li>brightharbourevents.co.uk
      <svg viewBox="0 0 16 16" aria-hidden="true"><circle cx="8" cy="8" r="7" fill="var(--icon-teal)"/><path d="M1 8h14M8 1c-3 3.5-3 10.5 0 14M8 1c3 3.5 3 10.5 0 14" stroke="#fff" stroke-width="1" fill="none"/></svg>
    </li>
  </ul>
</section>

<section class="card card--brands" aria-label="Brand side">
  <div class="brands">
    <p class="brand brand--events">Bright Harbour Events</p>
    <span class="brands__divider" aria-hidden="true"></span>
    <p class="brand brand--bloom">Quiet Meadow Bloom</p>
  </div>
</section>

</body>
</html>
```